Company Gift Card Designs

I would like to have 2 gift cards designed.

Both cards need to be in our company colors and have a non-white background. Both will need to follow the attached spec sheet from the card vendor.

Card 1 - will need to have the words Thank you on the card and use the KTB Logo

Card 2 - will need to have both the KTB logo and the Orb482 Logo incorporated into the design.

```html
<!DOCTYPE html>
<html lang="en">
<head>
<meta charset="utf-8">
<title>KTB Gift Cards</title>
<link rel="stylesheet" href="https://fonts.googleapis.com/css2?family=Kaushan+Script&family=Rubik:wght@800;900&family=Montserrat:wght@500&family=Roboto+Condensed:wght@700&display=swap">
<style>
  :root {
    --page: #ffffff;
    --blue: #2c8bc4;
    --blue-light: #3a92c9;
    --blue-deep: #1f76b0;
    --red: #c6303a;
    --ribbon: #e0261c;
    --ribbon-dark: #a8140e;
    --white: #ffffff;
  }
  * { box-sizing: border-box; margin: 0; padding: 0; }
  html, body {
    width: 748px;
    height: 1200px;
    overflow: hidden;
    background: var(--page);
  }
  .sheet {
    position: relative;
    width: 748px;
    height: 1200px;
  }
  .card {
    position: absolute;
    left: 54px;
    width: 640px;
    height: 402px;
    overflow: hidden;
    color: var(--white);
    text-align: center;
  }
  .card--thanks-duo { top: 150px; background: var(--red); }
  .card--thanks-solo { top: 640px; background: var(--blue); }

  .card__band {
    position: absolute;
    left: 0; top: 0;
    width: 100%;
    height: 168px;
    background: var(--blue-light);
  }

  .bow {
    position: absolute;
    background:
      radial-gradient(circle at 50% 50%, var(--ribbon) 0 34%, var(--ribbon-dark) 62%, transparent 64%);
  }
  .card--thanks-duo .bow--left  { left: 0; top: 0; width: 120px; height: 110px; }
  .card--thanks-duo .bow--right { right: 0; top: 0; width: 120px; height: 110px; }
  .card--thanks-solo .bow--left { left: 0; top: 0; width: 170px; height: 160px; }

  .logo-row {
    position: absolute;
    left: 0; right: 0;
    display: flex;
    justify-content: center;
    align-items: center;
    gap: 34px;
  }
  .card--thanks-duo .logo-row { top: 28px; }
  .card--thanks-solo .logo-row { top: 26px; }
  .brand {
    display: flex;
    align-items: center;
    gap: 8px;
    font-family: "Rubik", sans-serif;
    font-weight: 900;
    font-size: 50px;
    line-height: 1;
    letter-spacing: -1px;
    color: var(--white);
  }
  .brand__dot {
    width: 14px; height: 14px;
    border-radius: 50%;
    background: var(--white);
  }

  .thanks {
    position: absolute;
    left: 0; right: 0;
    font-family: "Kaushan Script", cursive;
    font-size: 92px;
    line-height: 1;
    color: var(--white);
  }
  .card--thanks-duo .thanks {
    top: 110px;
    text-shadow:
      0 0 0 var(--blue-deep),
      4px 4px 0 var(--blue-deep), -4px 4px 0 var(--blue-deep),
      4px -4px 0 var(--blue-deep), -4px -4px 0 var(--blue-deep),
      0 6px 0 var(--blue-deep), 6px 0 0 var(--blue-deep),
      -6px 0 0 var(--blue-deep), 0 -6px 0 var(--blue-deep);
  }
  .card--thanks-solo .thanks { top: 118px; }

  .giftcard {
    position: absolute;
    left: 0; right: 0;
    top: 236px;
    font-family: "Rubik", sans-serif;
    font-weight: 900;
    font-size: 38px;
    line-height: 1;
    letter-spacing: 0.5px;
  }
  .blurb {
    position: absolute;
    left: 60px; right: 60px;
    top: 284px;
    font-family: "Montserrat", sans-serif;
    font-weight: 500;
    font-size: 12.6px;
    line-height: 16px;
  }
  .tag {
    position: absolute;
    left: 208px;
    top: 344px;
    width: 224px;
    height: 31px;
    border-radius: 16px;
    background: var(--white);
    font-family: "Roboto Condensed", sans-serif;
    font-weight: 700;
    font-size: 17px;
    line-height: 31px;
  }
  .card--thanks-duo .tag { color: var(--red); }
  .card--thanks-solo .tag { color: var(--blue); }
</style>
</head>
<body>
<main class="sheet">

  <section class="card card--thanks-duo" aria-label="Gift card with KTB and Orb482">
    <div class="card__band"></div>
    <div class="bow bow--left" role="img" aria-label="Red satin ribbon bow on the corner"></div>
    <div class="bow bow--right" role="img" aria-label="Red satin ribbon bow on the corner"></div>
    <div class="logo-row">
      <span class="brand"><span class="brand__dot"></span>KTB</span>
      <span class="brand">Orb482</span>
    </div>
    <h2 class="thanks">Thank you</h2>
    <p class="giftcard">GIFTCARD</p>
    <p class="blurb">Lorem ipsum dolor sit amet, consectetur adipiscing elit, sed do eiusmod tempor incididunt ut labore et dolore magna aliqua. Quis ipsum suspendisse ultrices gravida. Risus commodo viverra maecenas accumsan lacus vel facilisis.</p>
    <p class="tag">NORTHFIELD RESTORATION</p>
  </section>

  <section class="card card--thanks-solo" aria-label="Thank you gift card with KTB">
    <div class="bow bow--left" role="img" aria-label="Red satin ribbon bow on the corner"></div>
    <div class="logo-row">
      <span class="brand"><span class="brand__dot"></span>KTB</span>
    </div>
    <h2 class="thanks">Thank you</h2>
    <p class="giftcard">GIFTCARD</p>
    <p class="blurb">Lorem ipsum dolor sit amet, consectetur adipiscing elit, sed do eiusmod tempor incididunt ut labore et dolore magna aliqua. Quis ipsum suspendisse ultrices gravida. Risus commodo viverra maecenas accumsan lacus vel facilisis.</p>
    <p class="tag">NORTHFIELD RESTORATION</p>
  </section>

</main>
</body>
</html>
```